Product label for herbal salves, lotions, soaps and tinctures

We need a very simple, clean and organic looking label that can be used for an ointment jar, a lotion bottle and a dropper bottle.
We have an existing logo (see attached). We like the colors white, olive green, gold and black. It needs to include product name as dominant and logo. It also needs to include an ingredient list, and usage statement. Include weight of product, distributed by, made in the USA, and QVX statement.
Example of what needs to be present:
Logo
Name: Tranquil Ease Blend
Used for: For Muscle Aches, Arthritis, Tendonitis, Headaches
To Use: For muscle aches, arthritis and tendonitis, massage into affected area. For tension headache apply to neck, temples and forehead.
Store in a cool and dry place, away from direct heat and sunlight.
Weight of product: 1.75
DIST. BY: Copper Brook Herbal
Made in the USA
This product is not intended to diagnose, treat, cure
or prevent any disease. Not regulated
by the QVX. Please consult your health care practitioner
before using product. Discontinue use if any adverse reaction occurs.
Ingredient list:
Wildcrafted Ingredients:
Ashwagandha Root, Peppermint Leaf, Hops Flowers, St. John’s Wort Herb, Arnica Flowers, Green Tea Leaf, Alfalfa Leaf, Dandelion Root, Burdock Root, Chickweed Herb, Chaparral Leaf, Yarrow Flowers, Boneset Herb, Moringa Leaf, Meadowsweet Herb, Nettle Leaf
Organic Ingredients:
Olive Oil, Aloe Leaf, Sweet Birch Bark, Helichrysum Flowers, Holy Basil Leaf, Borage Herb, Ginger Root, Angelica Root, White Willow Bark, Mustard Seed, Beeswax, Vitamin E, Essential Oils
Dimensions of Jar:
Circumference: 7 in.
Height: 1 in.

```html
<!DOCTYPE html>
<html lang="en">
<head>
<meta charset="utf-8">
<title>Tranquil Ease Blend – Jar Label</title>
<link rel="stylesheet" href="https://fonts.googleapis.com/css2?family=Noto+Sans:wght@400;500;600&family=Rozha+One&display=swap">
<style>
  :root {
    --olive: #6f7741;
    --olive-deep: #6b7530;
    --gold: #d4a24c;
    --gold-text: #c9922b;
    --ink: #1b1b1b;
    --paper: #ffffff;
    --stage: #eeeee8;
  }
  * { box-sizing: border-box; margin: 0; padding: 0; }
  html, body { width: 1200px; height: 786px; overflow: hidden; }
  body {
    background: var(--stage);
    font-family: "Noto Sans", Arial, sans-serif;
    color: var(--ink);
    position: relative;
  }
  .label {
    position: absolute;
    left: 0; top: 269px;
    width: 1200px; height: 248px;
  }
  .band { position: absolute; left: 0; width: 100%; background: var(--gold); }
  .band--top { top: 0; height: 22px; }
  .band--bottom { bottom: 0; height: 26px; }
  .panel {
    position: absolute; left: 0; top: 22px;
    width: 100%; height: 200px;
    background: var(--paper);
    overflow: hidden;
  }
  .botanical {
    position: absolute;
    background: linear-gradient(180deg, rgba(111,119,65,0) 0%, rgba(111,119,65,0.22) 100%);
  }
  .botanical--left { left: 350px; top: 160px; width: 240px; height: 40px; }
  .botanical--right { left: 830px; top: 112px; width: 370px; height: 88px;
    background: linear-gradient(200deg, rgba(111,119,65,0.08) 0%, rgba(111,119,65,0.3) 100%); }

  .info {
    position: absolute; left: 29px; top: 16px; width: 326px;
    display: flex; flex-direction: column;
  }
  .ingredients { font-size: 9.5px; line-height: 12.2px; }
  .ingredients__heading { color: var(--olive-deep); font-weight: 600; font-size: 10px; }
  .ingredients__group { color: var(--gold-text); font-weight: 600; font-size: 10px; }
  .ingredients__line {
    display: block; white-space: nowrap;
    text-align: justify; text-align-last: justify;
  }
  .ingredients__line--last { text-align-last: left; }

  .info__footer {
    margin-top: 6px;
    display: flex; align-items: flex-start; gap: 11px;
  }
  .distributor {
    font-size: 10px; line-height: 12.2px; letter-spacing: 0.6px;
    white-space: nowrap;
  }
  .distributor strong { font-weight: 600; }
  .storage {
    margin-top: 3px;
    width: 189px; height: 35px;
    border: 1.3px solid var(--ink);
    padding: 4px 0 0 8px;
    font-size: 9.8px; line-height: 12.2px; font-weight: 500;
    white-space: nowrap;
  }

  .brand {
    position: absolute; left: 398px; top: 38px; width: 152px;
    font-family: "Rozha One", Georgia, serif;
    color: var(--olive-deep);
    font-size: 30px; line-height: 30px;
    text-align: center;
  }
  .brand__mark {
    display: block; width: 10px; height: 10px; border-radius: 50%;
    background: var(--olive-deep); margin: 0 auto 6px;
  }

  .product {
    position: absolute; left: 585px; top: 8px; width: 228px;
  }
  .product__head { position: relative; }
  .product__name {
    font-family: "Rozha One", Georgia, serif;
    color: var(--gold-text);
    font-size: 33px; line-height: 31px; font-weight: 400;
    letter-spacing: 0.4px;
  }
  .product__weight {
    position: absolute; right: 0; bottom: 2px;
    font-size: 12px; line-height: 14px; font-weight: 500;
  }
  .product__rule { margin-top: 2px; height: 2px; background: var(--olive-deep); }
  .usage { margin-top: 7px; font-size: 10.3px; line-height: 12.2px; letter-spacing: 0.6px; }
  .usage__title { color: var(--olive); font-weight: 400; letter-spacing: 1px; }
  .usage__text { font-weight: 600; }

  .disclaimer {
    position: absolute; left: 907px; top: 24px; width: 280px;
    font-size: 10px; line-height: 12.2px; letter-spacing: 0.2px;
    white-space: nowrap;
  }
  .disclaimer span { display: block; }
</style>
</head>
<body>
  <section class="label" aria-label="Tranquil Ease Blend jar label">
    <div class="band band--top"></div>
    <div class="panel">
      <div class="botanical botanical--left" role="img" aria-label="Engraved olive branch and herb sprig illustration"></div>
      <div class="botanical botanical--right" role="img" aria-label="Engraved olive branches with fruit illustration"></div>

      <div class="info">
        <div class="ingredients">
          <p class="ingredients__heading">Ingredient list:</p>
          <p class="ingredients__group">Wildcrafted Ingredients:</p>
          <p>
            <span class="ingredients__line">Ashwagandha Root, Peppermint Leaf, Hops Flowers, St. John’s Wort</span>
            <span class="ingredients__line">Herb, Arnica Flowers, Green Tea Leaf, Alfalfa Leaf, Dandelion Root,</span>
            <span class="ingredients__line">Burdock Root, Chickweed Herb, Chaparral Leaf, Yarrow Flowers,</span>
            <span class="ingredients__line ingredients__line--last">Boneset Herb, Moringa Leaf, Meadowsweet Herb, Nettle Leaf</span>
          </p>
          <p class="ingredients__group">Organic Ingredients:</p>
          <p>
            <span class="ingredients__line">Olive Oil, Aloe Leaf, Sweet Birch Bark, Helichrysum Flowers, Holy</span>
            <span class="ingredients__line">Basil Leaf, Borage Herb, Ginger Root, Angelica Root, White Willow</span>
            <span class="ingredients__line ingredients__line--last">Bark, Mustard Seed, Beeswax, Vitamin E, Essential Oils</span>
          </p>
        </div>
        <div class="info__footer">
          <div class="distributor">
            <p>Distributed by:</p>
            <p><strong>Copper Brook Herbal</strong></p>
            <p><strong>Made in the USA</strong></p>
          </div>
          <div class="storage">Store in a cool and dry place,<br>away from direct heat and sunlight.</div>
        </div>
      </div>

      <div class="brand"><span class="brand__mark"></span>Copper Brook<br>Herbal</div>

      <div class="product">
        <div class="product__head">
          <h1 class="product__name">Tranquil Ease<br>Blend</h1>
          <span class="product__weight">1.75 oz</span>
        </div>
        <div class="product__rule"></div>
        <div class="usage">
          <p class="usage__title">How to Use :</p>
          <p class="usage__text">For muscle aches, arthritis and<br>tendonitis, massage into affected area.<br>For tension headache apply to neck,<br>temples and forehead.</p>
        </div>
      </div>

      <div class="disclaimer">
        <span>This product is not intended to diagnose, treat, cure</span>
        <span>or prevent any disease.</span>
        <span>Not regulated by the QVX.</span>
        <span>Please consult your health care practitioner</span>
        <span>before using product.</span>
        <span>Discontinue use if any adverse reaction occurs.</span>
      </div>
    </div>
    <div class="band band--bottom"></div>
  </section>
</body>
</html>
```